Company Website for Varnoth Signal, an open source data analytics company focused on relationship and li

I need a company/brand website for our new startup, Varnoth Signal LLC. We are a company focused on using life pattern analysis techniques, looking at relationships and how relationships, attributes, and activity cluster to infer aggregate information about individuals and groups. Our focus is on improving the digital advertising market.

We have a company logo which I will upload shortly.

Target Market(s)

Digital Advertising

Number of Pages Required

3 page

Font styles to use
Sans Serif

Requirements
Must have
• An main page, about us, contact page.
Nice to have
• Varnoth Signal relies on state of the art analytics applied to a the digital marketing space. While it is heavy in science, we also understand the art of influence. The website should have a scientific edge but also a flair that illustrates our focus on applying the hard science and analytics to influencing the behavior of people.

```html
<!DOCTYPE html>
<html lang="en">
<head>
<meta charset="utf-8">
<title>Varnoth Signal</title>
<link href="https://fonts.googleapis.com/css2?family=Poppins:wght@400;500;600;700&display=swap" rel="stylesheet">
<style>
:root{
  --orange:#f5a035;
  --blue:#2a9fd8;
  --ink:#111111;
  --text:#333333;
  --muted:#f6f6f6;
  --white:#ffffff;
  --footer:#0d0d0d;
}
*{margin:0;padding:0;box-sizing:border-box}
html,body{width:1200px;height:2899px;overflow:hidden}
body{position:relative;background:var(--white);font-family:'Poppins',sans-serif;color:var(--text)}
.btn{position:absolute;display:flex;align-items:center;justify-content:center;border-radius:16px;font-size:9px;font-weight:600;letter-spacing:.5px;text-transform:uppercase;color:var(--white);background:var(--orange)}
.btn-ghost{background:transparent;border:2px solid var(--white)}

/* header */
.site-header{position:absolute;left:0;top:0;width:1200px;height:75px;background:var(--white);border-top:2px solid #ddd}
.brand{position:absolute;left:232px;top:24px;display:flex;align-items:center;gap:8px;font-size:20px;font-weight:700;color:var(--blue)}
.brand-dot{width:12px;height:12px;border-radius:50%;background:var(--orange)}
.nav a{position:absolute;top:34px;font-size:11px;color:var(--ink);text-decoration:none}
.nav .active{color:var(--blue)}

/* hero */
.hero{position:absolute;left:0;top:75px;width:1200px;height:501px;background:linear-gradient(120deg,#3b3f44 0%,#5a5d60 45%,#2c2f33 100%)}
.hero-shade{position:absolute;inset:0;background:rgba(0,0,0,.35)}
.hero-kicker{position:absolute;top:105px;width:1200px;text-align:center;font-size:16px;color:var(--white)}
.hero-title{position:absolute;top:150px;width:1200px;text-align:center;font-size:52px;line-height:56px;font-weight:700;color:var(--white)}
.hero-text{position:absolute;left:280px;top:294px;width:640px;text-align:center;font-size:10px;line-height:17px;color:var(--white)}
.hero-dots{position:absolute;left:958px;top:180px;display:flex;flex-direction:column;gap:6px}
.hero-dots span{width:7px;height:7px;border:1px solid var(--white)}
.hero-dots span:first-child{background:var(--white)}

/* about */
.eyebrow{position:absolute;font-size:10px;font-weight:500;color:var(--blue);text-transform:uppercase}
.about-title{position:absolute;left:230px;top:640px;width:362px;text-align:right;font-size:25px;line-height:33px;font-weight:700;color:var(--ink)}
.about-text{position:absolute;left:220px;top:756px;width:372px;text-align:right;font-size:10px;line-height:16px}
.photo{position:absolute}
.who-text{position:absolute;left:609px;top:900px;width:358px;font-size:11px;line-height:17.5px;color:var(--ink)}

/* services */
.solutions{position:absolute;left:0;top:1159px;width:1200px;height:553px;background:var(--muted)}
.section-title{position:absolute;width:1200px;text-align:center;font-size:26px;font-weight:700;color:var(--ink)}
.section-text{position:absolute;left:350px;width:500px;text-align:center;font-size:10.5px;line-height:19px;color:var(--ink)}
.card{position:absolute;background:var(--white);box-shadow:0 2px 10px rgba(0,0,0,.06)}
.card-photo{position:absolute;left:0;top:0;width:100%}
.card-title{position:absolute;left:24px;font-size:14px;font-weight:600;color:var(--ink)}
.card-text{position:absolute;left:24px;width:200px;font-size:10px;line-height:18px;color:var(--ink)}

/* why */
.why-photo{position:absolute;left:0;top:1712px;width:590px;height:612px;background:linear-gradient(135deg,#c9d9e6 0%,#9fb3c4 40%,#3e5a7a 100%)}
.why-panel{position:absolute;left:590px;top:1712px;width:610px;height:612px;background:var(--orange)}
.why-title{position:absolute;left:80px;top:58px;font-size:28px;font-weight:600;color:var(--white)}
.why-item{position:absolute;left:80px;width:400px}
.why-item svg{position:absolute;left:0;top:2px}
.why-item h3{position:absolute;left:45px;top:0;font-size:17px;font-weight:600;color:var(--white)}
.why-item p{position:absolute;left:45px;top:28px;width:200px;font-size:10px;line-height:19px;color:var(--white)}

/* team */
.member{position:absolute;top:2483px;width:231px;height:307px;background:var(--white);box-shadow:0 2px 12px rgba(0,0,0,.08)}
.member-photo{position:absolute;left:0;top:0;width:231px;height:232px}
.member-name{position:absolute;left:24px;top:251px;font-size:14px;font-weight:600;color:var(--ink)}
.member-role{position:absolute;left:24px;top:274px;font-size:10.5px;color:var(--ink)}

/* footer */
.site-footer{position:absolute;left:0;top:2836px;width:1200px;height:63px;background:var(--footer)}
.site-footer small{position:absolute;left:234px;top:26px;font-size:8px;color:#777}
.footer-nav a{position:absolute;top:26px;font-size:9px;color:#555;text-decoration:none}
</style>
</head>
<body>

<header class="site-header">
  <div class="brand"><span>Varnoth Signal</span><span class="brand-dot"></span></div>
  <nav class="nav">
    <a class="active" style="left:688px">HOME</a>
    <a style="left:738px">ABOUT US</a>
    <a style="left:808px">Contact us</a>
  </nav>
  <div class="btn" style="left:898px;top:27px;width:76px;height:28px">Signup</div>
</header>

<section class="hero">
  <div class="hero-photo" role="img" aria-label="Team working around a table in a modern glass meeting room" style="position:absolute;inset:0"></div>
  <div class="hero-shade"></div>
  <p class="hero-kicker">Lorem Ipsum Dolor Sit World</p>
  <h1 class="hero-title">We Create value Earlier<br>More Reliably</h1>
  <p class="hero-text">Lorem ipsum dolor sit amet, consectetur adipiscing elit. Ut facilisis et enim id luctus. In hac habitasse platea dictumst. Vestibulum aliquam, urna ac vestibulum sagittis, est quam tincidunt sem, vitae faucibus nunc elit vel libero.</p>
  <div class="btn" style="left:468px;top:363px;width:125px;height:30px">Learn More</div>
  <div class="btn btn-ghost" style="left:609px;top:363px;width:123px;height:30px">Contact Us</div>
  <div class="hero-dots"><span></span><span></span><span></span><span></span><span></span></div>
</section>

<section class="about">
  <span class="eyebrow" style="left:555px;top:619px">About</span>
  <h2 class="about-title">We Create Value Earlier More Reliably, Why &nbsp;We Best In Consulting</h2>
  <p class="about-text">Lorem ipsum dolor sit amet, consectetur adipiscing elit. Ut facilisis et enim id luctus. In hac habitasse platea dictumst. Vestibulum aliquam, urna ac vestibulum sagittis, est quam tincidunt sem, vitae faucibus nunc elit vel libero.</p>
  <div class="photo" role="img" aria-label="Business partners shaking hands in an office" style="left:609px;top:620px;width:356px;height:236px;background:linear-gradient(135deg,#dfe6ee 0%,#8ea4bd 55%,#1f3552 100%)"></div>
  <div class="photo" role="img" aria-label="Colleagues discussing at a bright meeting table" style="left:234px;top:881px;width:356px;height:236px;background:linear-gradient(135deg,#e8eef3 0%,#b7c6d3 50%,#54657a 100%)"></div>
  <span class="eyebrow" style="left:609px;top:877px">Who We Are</span>
  <p class="who-text">Lorem ipsum dolor sit amet, consectetur adipiscing elit. Ut facilisis et enim id luctus. In hac habitasse platea dictumst. Vestibulum aliquam, urna ac vestibulum sagittis, est quam tincidunt sem, vitae faucibus nunc elit vel libero. Nulla facilisi. Etiam commodo cursus lobortis. Vestibulum ante ipsum primis in faucibus orci luctus et ultrices posuere cubilia Curae; Curabitur id semper justo, luctus dapibus lorem. Aliquam at diam ullamcorper, sagittis dui vel, ullamcorper nulla.</p>
  <div class="btn" style="left:609px;top:1051px;width:125px;height:29px">Learn More</div>
</section>

<section class="solutions">
  <h2 class="section-title" style="top:41px">We Have The Right Solutions</h2>
  <p class="section-text" style="top:92px">Nulla facilisi. Etiam commodo cursus lobortis. Vestibulum ante ipsum primis in faucibus orci luctus et ultrices posuere cubilia Curae; Curabitur id semper justo, luctus dapibus lorem.</p>

  <article class="card" style="left:234px;top:161px;width:230px;height:342px">
    <div class="card-photo" role="img" aria-label="Designers reviewing work at a laptop" style="height:172px;background:linear-gradient(135deg,#c8d2db,#6d7d8c)"></div>
    <h3 class="card-title" style="top:198px">Graphic Design</h3>
    <p class="card-text" style="top:224px">Nulla facilisi. Etiam commodo cursus lobortis. Vestibulum ante ipsum primis in faucibus orci luctus etlorem.</p>
    <div class="btn" style="left:23px;top:288px;width:97px;height:30px">Learn More</div>
  </article>
  <article class="card" style="left:484px;top:161px;width:231px;height:342px">
    <div class="card-photo" role="img" aria-label="Business meeting in a conference room" style="height:172px;background:linear-gradient(135deg,#e4e4e4,#5c5c5c)"></div>
    <h3 class="card-title" style="top:198px">Web Design</h3>
    <p class="card-text" style="top:224px">Nulla facilisi. Etiam commodo cursus lobortis. Vestibulum ante ipsum primis in faucibus orci luctus etlorem.</p>
    <div class="btn" style="left:23px;top:288px;width:97px;height:30px">Learn More</div>
  </article>
  <article class="card" style="left:734px;top:161px;width:232px;height:342px">
    <div class="card-photo" role="img" aria-label="Overhead view of a team working around a table" style="height:172px;background:linear-gradient(135deg,#5a6570,#2d343b)"></div>
    <h3 class="card-title" style="top:198px">Web Development</h3>
    <p class="card-text" style="top:224px">Nulla facilisi. Etiam commodo cursus lobortis. Vestibulum ante ipsum primis in faucibus orci luctus etlorem.</p>
    <div class="btn" style="left:23px;top:288px;width:97px;height:30px">Learn More</div>
  </article>
</section>

<div class="why-photo" role="img" aria-label="Two colleagues reviewing documents and a tablet"></div>
<section class="why-panel">
  <h2 class="why-title">Why You Choose Us?</h2>
  <div class="why-item" style="top:138px">
    <svg width="32" height="32" viewBox="0 0 32 32" fill="none" stroke="#fff" stroke-width="1.5"><rect x="3" y="5" width="22" height="22" rx="2"/><path d="M8 20l5-6 4 4 6-8"/><circle cx="26" cy="8" r="3"/></svg>
    <h3>Digital Marketing</h3>
    <p>Nulla facilisi. Etiam commodo cursus lobortis. Vestibulum ante ipsum primis in faucibus orci luctus etlorem.</p>
  </div>
  <div class="why-item" style="top:250px">
    <svg width="32" height="32" viewBox="0 0 32 32" fill="none" stroke="#fff" stroke-width="1.5"><rect x="3" y="4" width="24" height="18" rx="2"/><path d="M10 27h10M15 22v5M8 16v-4M13 16v-7M18 16v-5M23 16v-8"/></svg>
    <h3>Digital Marketing</h3>
    <p>Nulla facilisi. Etiam commodo cursus lobortis. Vestibulum ante ipsum primis in faucibus orci luctus etlorem.</p>
  </div>
  <div class="why-item" style="top:362px">
    <svg width="32" height="32" viewBox="0 0 32 32" fill="none" stroke="#fff" stroke-width="1.5"><circle cx="13" cy="17" r="9"/><path d="M13 8v9h9"/><rect x="21" y="3" width="8" height="8" rx="1"/></svg>
    <h3>Digital Marketing</h3>
    <p>Nulla facilisi. Etiam commodo cursus lobortis. Vestibulum ante ipsum primis in faucibus orci luctus etlorem.</p>
  </div>
  <div class="why-item" style="top:474px">
    <svg width="32" height="32" viewBox="0 0 32 32" fill="none" stroke="#fff" stroke-width="1.5"><rect x="3" y="6" width="24" height="16" rx="2"/><path d="M7 26h16M9 17l4-5 4 3 5-5"/></svg>
    <h3>Digital Marketing</h3>
    <p>Nulla facilisi. Etiam commodo cursus lobortis. Vestibulum ante ipsum primis in faucibus orci luctus etlorem.</p>
  </div>
</section>

<section class="team">
  <h2 class="section-title" style="top:2363px">We Have The Right Solutions</h2>
  <p class="section-text" style="top:2414px">Nulla facilisi. Etiam commodo cursus lobortis. Vestibulum ante ipsum primis in faucibus orci luctus et ultrices posuere cubilia Curae; Curabitur id semper justo, luctus dapibus lorem.</p>
  <article class="member" style="left:234px">
    <div class="member-photo" role="img" aria-label="Portrait of a team member" style="background:linear-gradient(135deg,#a08a78,#3a2f2a)"></div>
    <h3 class="member-name">John Doe</h3><p class="member-role">Producer</p>
  </article>
  <article class="member" style="left:484px">
    <div class="member-photo" role="img" aria-label="Portrait of a team member" style="background:linear-gradient(135deg,#c9b6a5,#6e5a4d)"></div>
    <h3 class="member-name">John Doe</h3><p class="member-role">Producer</p>
  </article>
  <article class="member" style="left:735px">
    <div class="member-photo" role="img" aria-label="Portrait of a team member" style="background:linear-gradient(135deg,#d8d2c8,#5d5852)"></div>
    <h3 class="member-name">John Doe</h3><p class="member-role">Producer</p>
  </article>
</section>

<footer class="site-footer">
  <small>© 2018 VARNOTH SIGNAL. ALL RIGHTS RESERVED.</small>
  <nav class="footer-nav">
    <a style="left:797px">HOME</a>
    <a style="left:846px">ABOUT US</a>
    <a style="left:914px">Contact us</a>
  </nav>
</footer>

</body>
</html>
```